Landing Page / Waitlist

I would like a landing page for people to sign up for a waiting list. The text on the page should include (but is not limited to):
1) Main point: The accounting system you'll love
2) Secondary points:
a. Ruthlessly efficient
b. Quietly intelligent
c. Driven by AI
I've attached a file of our logo

The design should be simple, clean, and innovative - this is an ai company

```html
<!DOCTYPE html>
<html lang="en">
<head>
<meta charset="utf-8">
<title>Tallywise – Waitlist Landing Page</title>
<link href="https://fonts.googleapis.com/css2?family=Poppins:wght@400;500;600;700&display=swap" rel="stylesheet">
<style>
  :root {
    --board: #c8c8c8;
    --blue: #00aeef;
    --blue-deep: #0a8df5;
    --ink: #111111;
    --muted: #555a60;
    --wordmark: #6d6d6d;
    --line: #cfd4da;
    --white: #ffffff;
  }
  * { margin: 0; padding: 0; box-sizing: border-box; }
  html, body { width: 738px; height: 1200px; overflow: hidden; }
  body {
    background: var(--board);
    font-family: "Poppins", sans-serif;
    position: relative;
  }
  .panel {
    position: absolute;
    left: 23px;
    width: 692px;
    height: 558px;
    background: var(--white);
    overflow: hidden;
    color: var(--ink);
  }
  .panel--light { top: 27px; background: linear-gradient(180deg, #fff 62%, #f3f6fb 100%); }
  .panel--dark {
    top: 614px;
    background: radial-gradient(ellipse at 75% 45%, #0d1c26 0%, #03080c 55%, #000 100%);
    color: var(--white);
  }
  .brand {
    position: absolute; left: 83px; top: 58px;
    display: flex; align-items: center; gap: 6px;
    font-size: 15px; font-weight: 600; color: var(--wordmark);
  }
  .brand__dot { width: 10px; height: 10px; border-radius: 50%; background: var(--blue); }
  .hero-title {
    position: absolute; left: 83px; top: 103px;
    font-size: 27px; line-height: 33px; font-weight: 700;
  }
  .hero-title__accent { color: var(--blue); display: flex; align-items: center; gap: 9px; }
  .hero-title__mark { width: 14px; height: 14px; border-radius: 50%; background: var(--blue); }
  .hero-title__light { font-weight: 500; }
  .email-field {
    position: absolute; left: 83px; top: 188px; width: 276px; height: 27px;
    border: 1px solid var(--line); border-radius: 14px; background: var(--white);
    display: flex; align-items: center; gap: 4px; padding-left: 16px;
    font-size: 7.5px; color: var(--muted);
  }
  .waitlist-button {
    position: absolute; left: 83px; top: 228px; width: 134px; height: 27px;
    border-radius: 14px; background: linear-gradient(90deg, var(--blue), var(--blue-deep));
    color: var(--white); font-size: 8.5px; font-weight: 700; letter-spacing: 0.1px;
    display: flex; align-items: center; justify-content: space-between; padding: 0 10px 0 15px;
  }
  .brand-mark-area {
    position: absolute; left: 412px; top: 27px; width: 196px; height: 249px;
    background: linear-gradient(160deg, #00b8ff 0%, #0a8df5 100%);
    border-radius: 6px; opacity: 0.92;
  }
  .section-title {
    position: absolute; left: 0; right: 0; top: 311px; text-align: center;
    font-size: 22px; font-weight: 700;
  }
  .section-title__accent { color: var(--blue); font-weight: 500; }
  .feature {
    position: absolute; width: 170px; text-align: center;
  }
  .feature__icon { display: block; margin: 0 auto; width: 60px; height: 68px; }
  .feature__title { font-size: 10.5px; font-weight: 500; margin-top: 9px; }
  .feature__text { font-size: 8px; line-height: 13.5px; color: var(--muted); margin-top: 3px; }
  .panel--dark .feature__text { color: var(--white); }
  .feature--efficient { left: 81px; top: 366px; }
  .feature--intelligent { left: 267px; top: 358px; }
  .feature--ai { left: 447px; top: 360px; }
  .site-footer {
    position: absolute; left: 0; bottom: 0; width: 100%; height: 25px;
    background: var(--blue-deep); color: var(--white);
    font-size: 8px; display: flex; align-items: center; justify-content: center;
  }
</style>
</head>
<body>

<section class="panel panel--light">
  <div class="brand"><span class="brand__dot"></span>Tallywise</div>
  <h1 class="hero-title">
    <span class="hero-title__accent"><span class="hero-title__mark"></span>The Accounting</span>
    System <span class="hero-title__light">You'll Love</span>
  </h1>
  <div class="email-field">
    <svg width="8" height="6" viewBox="0 0 8 6"><rect x="0.5" y="0.5" width="7" height="5" fill="none" stroke="currentColor" stroke-width="0.8"/><path d="M0.5 0.8 L4 3.3 L7.5 0.8" fill="none" stroke="currentColor" stroke-width="0.8"/></svg>
    Email Address
  </div>
  <div class="waitlist-button">JOIN THE WAITLIST
    <svg width="8" height="8" viewBox="0 0 8 8"><path d="M1 7 L7 1 M2.5 1 H7 V5.5" fill="none" stroke="#fff" stroke-width="1.1"/></svg>
  </div>
  <div class="brand-mark-area" role="img" aria-label="Large brand symbol area"></div>
  <h2 class="section-title"><span class="section-title__accent">Value</span> Proposition</h2>

  <div class="feature feature--efficient">
    <svg class="feature__icon" viewBox="0 0 60 68"><defs><linearGradient id="hexA" x1="0" y1="0" x2="1" y2="1"><stop offset="0" stop-color="#00b8ff"/><stop offset="1" stop-color="#0a7ff0"/></linearGradient></defs><polygon points="30,1 59,17.5 59,50.5 30,67 1,50.5 1,17.5" fill="none" stroke="#00c8ff" stroke-width="1.2"/><polygon points="30,4 56,19 56,49 30,64 4,49 4,19" fill="url(#hexA)"/><circle cx="30" cy="34" r="7" fill="none" stroke="#fff" stroke-width="3"/></svg>
    <div class="feature__title">Ruthlessly Efficient</div>
    <p class="feature__text">Automate busywork, streamline workflows,<br>and close books faster than ever.</p>
  </div>
  <div class="feature feature--intelligent">
    <svg class="feature__icon" viewBox="0 0 60 68"><polygon points="30,1 59,17.5 59,50.5 30,67 1,50.5 1,17.5" fill="none" stroke="#00c8ff" stroke-width="1.2"/><polygon points="30,4 56,19 56,49 30,64 4,49 4,19" fill="url(#hexA)"/><circle cx="30" cy="34" r="7" fill="none" stroke="#fff" stroke-width="3"/></svg>
    <div class="feature__title">Quietly Intelligent</div>
    <p class="feature__text">Smart suggestions, anomaly detection,<br>and predictive insights available only<br>when you need them.</p>
  </div>
  <div class="feature feature--ai">
    <svg class="feature__icon" viewBox="0 0 60 68"><polygon points="30,1 59,17.5 59,50.5 30,67 1,50.5 1,17.5" fill="none" stroke="#00c8ff" stroke-width="1.2"/><polygon points="30,4 56,19 56,49 30,64 4,49 4,19" fill="url(#hexA)"/><circle cx="30" cy="34" r="7" fill="none" stroke="#fff" stroke-width="3"/></svg>
    <div class="feature__title">AI-Driven</div>
    <p class="feature__text">Built from the ground up using modern<br>AI not just patched-on automation like<br>legacy systems.</p>
  </div>

  <footer class="site-footer">© 2025 Tallywise - All Rights Reserved</footer>
</section>

<section class="panel panel--dark">
  <div class="brand"><span class="brand__dot"></span>Tallywise</div>
  <h1 class="hero-title">
    <span class="hero-title__accent"><span class="hero-title__mark"></span>The Accounting</span>
    System <span class="hero-title__light">You'll Love</span>
  </h1>
  <div class="email-field">
    <svg width="8" height="6" viewBox="0 0 8 6"><rect x="0.5" y="0.5" width="7" height="5" fill="none" stroke="currentColor" stroke-width="0.8"/><path d="M0.5 0.8 L4 3.3 L7.5 0.8" fill="none" stroke="currentColor" stroke-width="0.8"/></svg>
    Email Address
  </div>
  <div class="waitlist-button">JOIN THE WAITLIST
    <svg width="8" height="8" viewBox="0 0 8 8"><path d="M1 7 L7 1 M2.5 1 H7 V5.5" fill="none" stroke="#fff" stroke-width="1.1"/></svg>
  </div>
  <div class="brand-mark-area" role="img" aria-label="Large brand symbol area"></div>
  <h2 class="section-title"><span class="section-title__accent">Value</span> Proposition</h2>

  <div class="feature feature--efficient">
    <svg class="feature__icon" viewBox="0 0 60 68"><polygon points="30,1 59,17.5 59,50.5 30,67 1,50.5 1,17.5" fill="none" stroke="#00c8ff" stroke-width="1.2"/><polygon points="30,4 56,19 56,49 30,64 4,49 4,19" fill="url(#hexA)"/><circle cx="30" cy="34" r="7" fill="none" stroke="#fff" stroke-width="3"/></svg>
    <div class="feature__title">Ruthlessly Efficient</div>
    <p class="feature__text">Automate busywork, streamline workflows,<br>and close books faster than ever.</p>
  </div>
  <div class="feature feature--intelligent">
    <svg class="feature__icon" viewBox="0 0 60 68"><polygon points="30,1 59,17.5 59,50.5 30,67 1,50.5 1,17.5" fill="none" stroke="#00c8ff" stroke-width="1.2"/><polygon points="30,4 56,19 56,49 30,64 4,49 4,19" fill="url(#hexA)"/><circle cx="30" cy="34" r="7" fill="none" stroke="#fff" stroke-width="3"/></svg>
    <div class="feature__title">Quietly Intelligent</div>
    <p class="feature__text">Smart suggestions, anomaly detection,<br>and predictive insights available only<br>when you need them.</p>
  </div>
  <div class="feature feature--ai">
    <svg class="feature__icon" viewBox="0 0 60 68"><polygon points="30,1 59,17.5 59,50.5 30,67 1,50.5 1,17.5" fill="none" stroke="#00c8ff" stroke-width="1.2"/><polygon points="30,4 56,19 56,49 30,64 4,49 4,19" fill="url(#hexA)"/><circle cx="30" cy="34" r="7" fill="none" stroke="#fff" stroke-width="3"/></svg>
    <div class="feature__title">AI-Driven</div>
    <p class="feature__text">Built from the ground up using modern<br>AI not just patched-on automation like<br>legacy systems.</p>
  </div>

  <footer class="site-footer">© 2025 Tallywise - All Rights Reserved</footer>
</section>

</body>
</html>
```